BOLD & MINIMALIST DESIGN NEEDED

We want a very bold but minimalistic business card design that is impactful and utilizes both sides of the business card. Our current logo is included for your use.

We want bold fonts and good use of negative space. We don't want the logo to overpower the design.

Target Market(s)

Professionals who are building new commercial buildings.

Industry/Entity Type

Construction

Contact Information for Business Card

Name, Title, email, office phone, cell phone, website

Font styles to use
Serif
Sans Serif

Requirements
Must have
• Bold design!

```html
<!DOCTYPE html>
<html lang="en">
<head>
<meta charset="utf-8">
<title>Ridgeline Design + Build — Business Card</title>
<link rel="stylesheet" href="https://fonts.googleapis.com/css2?family=Arimo:wght@400;700&display=swap">
<style>
  :root {
    --bg: #d9d9d9;
    --card-dark: #1f1f1f;
    --card-light: #ffffff;
    --green: #7cc242;
    --green-light: #c9e8a8;
    --ink: #1a1a1a;
    --ink-soft: #333333;
  }
  html, body {
    margin: 0;
    width: 1200px;
    height: 875px;
    overflow: hidden;
    background: var(--bg);
    font-family: "Arimo", Arial, sans-serif;
  }
  .canvas {
    position: relative;
    width: 1200px;
    height: 875px;
  }
  .card {
    position: absolute;
    top: 282px;
    width: 540px;
    height: 310px;
    border-radius: 18px;
    overflow: hidden;
    box-shadow: 0 8px 24px rgba(0,0,0,.18);
  }
  /* Back side */
  .card-back {
    left: 40px;
    background: var(--card-dark);
    display: flex;
    flex-direction: column;
    align-items: center;
    justify-content: center;
  }
  .brand-name {
    font-weight: 700;
    font-size: 48px;
    letter-spacing: 1px;
    text-transform: uppercase;
    line-height: 1;
    display: flex;
    align-items: center;
    gap: 12px;
  }
  .brand-mark-square {
    width: 26px;
    height: 26px;
    background: var(--green);
  }
  .card-back .brand-name { color: #ffffff; }
  .brand-tagline {
    margin-top: 10px;
    padding-top: 6px;
    border-top: 2px solid currentColor;
    font-size: 17px;
    letter-spacing: 7px;
    text-transform: uppercase;
  }
  .card-back .brand-tagline { color: #ffffff; }

  /* Front side */
  .card-front {
    left: 620px;
    background: var(--card-light);
  }
  .front-brand {
    position: absolute;
    left: 34px;
    top: 52px;
  }
  .front-brand .brand-name {
    font-size: 34px;
    color: var(--ink);
  }
  .front-brand .brand-tagline {
    font-size: 12px;
    letter-spacing: 6px;
    color: var(--ink);
    display: inline-block;
  }
  .decor-area {
    position: absolute;
    right: 0;
    top: 0;
    width: 190px;
    height: 250px;
    background: linear-gradient(160deg, var(--green-light) 0%, var(--green) 45%, var(--card-dark) 100%);
    border-bottom-left-radius: 190px 60px;
  }
  .accent-bar {
    position: absolute;
    left: 0;
    top: 168px;
    width: 12px;
    height: 34px;
    background: linear-gradient(90deg, var(--green), var(--green-light));
  }
  .person {
    position: absolute;
    left: 34px;
    top: 160px;
  }
  .person-name {
    font-weight: 700;
    font-size: 22px;
    color: var(--green);
    text-transform: uppercase;
    margin: 0;
  }
  .person-title {
    font-size: 14px;
    color: var(--ink-soft);
    margin: 2px 0 12px;
  }
  .contact-list {
    list-style: none;
    margin: 0;
    padding: 0;
    font-size: 13px;
    color: var(--ink-soft);
  }
  .contact-list li {
    display: flex;
    align-items: center;
    gap: 8px;
    margin-bottom: 4px;
  }
  .contact-icon {
    width: 11px;
    height: 11px;
    flex: none;
  }
</style>
</head>
<body>
<main class="canvas">

  <section class="card card-back" aria-label="Card back">
    <div class="brand-name"><span class="brand-mark-square"></span>Ridgeline</div>
    <div class="brand-tagline">Design + Build</div>
  </section>

  <section class="card card-front" aria-label="Card front">
    <div class="decor-area" role="img" aria-label="Brand decoration area in green and black"></div>

    <div class="front-brand">
      <div class="brand-name">Ridgeline</div>
      <div class="brand-tagline">Design + Build</div>
    </div>

    <div class="accent-bar"></div>

    <div class="person">
      <p class="person-name">Dana Whitford</p>
      <p class="person-title">Owner/CEO</p>
      <ul class="contact-list">
        <li>
          <svg class="contact-icon" viewBox="0 0 12 12"><path fill="#7cc242" d="M2 1h3l1 3-1.5 1a6 6 0 0 0 2.5 2.5L8 6l3 1v3a1 1 0 0 1-1 1A9 9 0 0 1 1 2a1 1 0 0 1 1-1z"/></svg>
          07 5120 4400
        </li>
        <li>
          <svg class="contact-icon" viewBox="0 0 12 12"><rect x="3" y="0.5" width="6" height="11" rx="1" fill="none" stroke="#7cc242" stroke-width="1.3"/><circle cx="6" cy="9.5" r=".8" fill="#7cc242"/></svg>
          0412 305 718
        </li>
        <li>
          <svg class="contact-icon" viewBox="0 0 12 12"><rect x="0.5" y="2" width="11" height="8" fill="#7cc242"/><path d="M0.5 2l5.5 4.5L11.5 2" fill="none" stroke="#fff" stroke-width="1"/></svg>
          info@ridgelinebuild.com
        </li>
        <li>
          <svg class="contact-icon" viewBox="0 0 12 12"><circle cx="6" cy="6" r="5.2" fill="none" stroke="#7cc242" stroke-width="1.3"/><path d="M1 6h10M6 1c2 2 2 8 0 10M6 1c-2 2-2 8 0 10" fill="none" stroke="#7cc242" stroke-width="1"/></svg>
          www.ridgelinebuild.com
        </li>
      </ul>
    </div>
  </section>

</main>
</body>
</html>
```